Communication and Marketing agency needs a new presentation card

We are a group of communication and marketing agencies specialized in companies that are in the logistics and industrial sector. The head agency is TELVANO Grupo and the group consists of 4 agencies: TELVANO Media, TELVANO Digital, TELVANO Research and DifundeEnPantalla. We hace 4 offices in Spain (Madrid, Barcelona, Valencia and Murcia). We are looking for a clean and attractive design that transmits our experience, brand presence in the market and knowledge to those who receive the card.It has to maintain the colors of the logo that is attached.
Target Market(s)
logistics and industrial sector
Marketing department
Contact Information for Business Card
Clean and attractive design

```html
<!DOCTYPE html>
<html lang="es">
<head>
<meta charset="utf-8">
<title>TELVANO Grupo – Tarjeta de presentación</title>
<link rel="stylesheet" href="https://fonts.googleapis.com/css2?family=Open+Sans:wght@400;600;700&display=swap">
<style>
  :root {
    --brand-red: #b21a26;
    --card-light: #e3e2e2;
    --ink-grey: #4a4a4a;
    --rule-grey: #b9b9b9;
    --stage: #3a3a3c;
    --white: #ffffff;
  }
  * { box-sizing: border-box; margin: 0; padding: 0; }
  html, body {
    width: 1200px; height: 896px; overflow: hidden;
    background: var(--stage);
    font-family: "Open Sans", Arial, sans-serif;
  }
  .sheet {
    width: 1200px; height: 896px;
    display: flex; align-items: center; justify-content: center; gap: 40px;
  }
  .card {
    position: relative;
    width: 540px; height: 340px;
    overflow: hidden;
    box-shadow: 0 8px 24px rgba(0,0,0,.35);
  }

  /* Front */
  .card--front { background: var(--card-light); }
  .card--front .base-band {
    position: absolute; left: 0; right: 0; bottom: 0; height: 14px;
    background: var(--brand-red);
  }
  .contact {
    position: absolute; left: 34px; top: 46px;
  }
  .contact__name {
    color: var(--brand-red); font-weight: 700; font-size: 21px;
    letter-spacing: .5px; text-transform: uppercase; line-height: 1;
  }
  .contact__role {
    color: var(--ink-grey); font-size: 14px; margin: 4px 0 10px;
  }
  .contact__list { list-style: none; }
  .contact__item {
    display: flex; align-items: center; gap: 8px;
    color: var(--ink-grey); font-size: 13.5px; line-height: 21px;
  }
  .contact__item svg { width: 12px; height: 12px; fill: var(--brand-red); flex: none; }

  .brand-main {
    position: absolute; right: 34px; top: 62px; text-align: right;
    color: var(--brand-red); font-weight: 600; line-height: 1;
  }
  .brand-main__name { font-size: 46px; letter-spacing: 3px; }
  .brand-main__sub { font-size: 24px; margin-top: 2px; }

  .divider {
    position: absolute; left: 250px; right: 34px; top: 176px;
    border-top: 1px solid var(--rule-grey);
  }
  .agencies {
    position: absolute; left: 200px; right: 34px; top: 196px;
    display: grid; grid-template-columns: 1fr 1fr; row-gap: 18px; column-gap: 14px;
  }
  .agency {
    font-weight: 600; font-size: 15px; line-height: 1; letter-spacing: .5px;
  }
  .agency--grey { color: var(--ink-grey); }
  .agency--red { color: var(--brand-red); }

  /* Back */
  .card--back {
    background: var(--brand-red);
    display: flex; flex-direction: column; align-items: center; justify-content: center;
    color: var(--white);
  }
  .brand-back { text-align: right; font-weight: 600; line-height: 1; }
  .brand-back__name { font-size: 54px; letter-spacing: 4px; }
  .brand-back__sub { font-size: 28px; margin-top: 2px; }
  .offices {
    margin-top: 34px; font-size: 14px; letter-spacing: 1px; text-transform: uppercase;
  }
</style>
</head>
<body>
<main class="sheet">
  <section class="card card--front" aria-label="Anverso de la tarjeta">
    <div class="contact">
      <p class="contact__name">Lucas Ferrer</p>
      <p class="contact__role">Managing Director</p>
      <ul class="contact__list">
        <li class="contact__item">
          <svg viewBox="0 0 12 12"><path d="M1 4c0-2 2-3 5-3s5 1 5 3v1H8V4H4v1H1z M2 6h8l1 5H1z"/></svg>055-987 654 321
        </li>
        <li class="contact__item">
          <svg viewBox="0 0 12 12"><path d="M3 0h6a1 1 0 0 1 1 1v10a1 1 0 0 1-1 1H3a1 1 0 0 1-1-1V1a1 1 0 0 1 1-1zm0 2v7h6V2z"/></svg>055-987 654 321
        </li>
        <li class="contact__item">
          <svg viewBox="0 0 12 12"><path d="M0 2h12v1L6 7 0 3z M0 4.5l6 4 6-4V10H0z"/></svg>hola@telvanomail.com
        </li>
        <li class="contact__item">
          <svg viewBox="0 0 12 12"><circle cx="6" cy="6" r="6"/></svg>www.telvanogrupo.com
        </li>
      </ul>
    </div>

    <div class="brand-main">
      <p class="brand-main__name">TELVANO</p>
      <p class="brand-main__sub">Grupo</p>
    </div>

    <div class="divider"></div>

    <div class="agencies">
      <p class="agency agency--grey">TELVANO Research</p>
      <p class="agency agency--grey">TELVANO Digital</p>
      <p class="agency agency--red">TELVANO Media</p>
      <p class="agency agency--red">DifundeEnPantalla</p>
    </div>

    <div class="base-band"></div>
  </section>

  <section class="card card--back" aria-label="Reverso de la tarjeta">
    <div class="brand-back">
      <p class="brand-back__name">TELVANO</p>
      <p class="brand-back__sub">Grupo</p>
    </div>
    <p class="offices">Madrid, Barcelona, Valencia, Murcia</p>
  </section>
</main>
</body>
</html>
```